Ferncliff Capital - Website Design

We need a website design for a new commercial real estate company called Ferncliff Capital. We're effectively commercial mortgage brokers connecting real estate investors to lenders. We need a website that is simple (not busy), elegant, professional, and user-friendly. A lot of the users will be in their 50's and less tech savvy, so a stream-lined design is best. The website will serve as a portal for lenders to review new financing opportunities, as well as for real estate investors to review terms from lenders.
Updates
Just uploaded our logo.
Target Market(s)
Commercial real estate investors and lenders
Industry/Entity Type
Real Estate
Number of Pages Required
1 page
Colors
Designer to choose colors to be used in the design.
Look and feel

```html
<!DOCTYPE html>
<html lang="en">
<head>
<meta charset="utf-8">
<title>Ferncliff Capital</title>
<link href="https://fonts.googleapis.com/css2?family=Roboto:ital,wght@0,400;0,500;0,700;1,400&display=swap" rel="stylesheet">
<style>
:root{
  --blue:#2a4f9e;
  --green:#1f6b1e;
  --dark:#2b2b2b;
  --ink:#333;
  --muted:#666;
  --light:#f7f7f7;
  --white:#fff;
}
*{box-sizing:border-box;margin:0;padding:0}
html,body{width:1200px;height:3020px;overflow:hidden}
body{font-family:'Roboto',Arial,sans-serif;color:var(--ink);background:var(--white);position:relative}
.abs{position:absolute}
.btn{position:absolute;background:var(--green);color:var(--white);font-size:12px;font-weight:500;border-radius:20px;display:flex;align-items:center;justify-content:center;letter-spacing:.3px}
.center{left:0;width:1200px;text-align:center}

.site-header{position:absolute;top:0;left:0;width:1200px;height:86px;background:var(--blue);color:var(--white)}
.brand{position:absolute;left:98px;top:31px;font-size:21px;font-weight:500;letter-spacing:.5px}
.nav{position:absolute;right:98px;top:36px;display:flex;gap:32px;font-size:12px;font-weight:500}

.hero{position:absolute;top:86px;left:0;width:1200px;height:458px;background:linear-gradient(180deg,#8c9a7e 0%,#b7b2a2 45%,#9b9a93 100%)}
.hero-box{position:absolute;left:342px;top:170px;width:630px;height:247px;background:rgba(40,40,40,.55)}
.hero-title{position:absolute;top:205px;font-size:46px;font-weight:700;color:var(--white)}
.hero-sub{position:absolute;top:270px;font-size:25px;color:var(--white)}

.section-title{position:absolute;font-size:30px;font-weight:500;color:var(--ink);letter-spacing:.3px}
.body-text{position:absolute;font-size:11.5px;line-height:26px;color:var(--muted)}

.contact-band{position:absolute;top:894px;left:0;width:1200px;height:241px;background:linear-gradient(90deg,#5b4a3c,#8a7d6f 50%,#4e4a48)}
.contact-band .veil{position:absolute;inset:0;background:rgba(30,30,30,.35)}
.email-input{position:absolute;background:var(--white);font-size:12px;color:#555;padding-left:12px;display:flex;align-items:center}
.btn-square{position:absolute;color:var(--white);font-size:12px;font-weight:500;display:flex;align-items:center;justify-content:center}

.what-we-do{position:absolute;top:1135px;left:0;width:1200px;height:451px;background:var(--light)}
.services{position:absolute;left:664px;top:1188px;width:437px;height:330px;background:linear-gradient(160deg,#4b4d52,#5d5a50 55%,#3e4a2c)}
.service{position:absolute;width:218px;text-align:center;color:var(--white)}
.service .cat{font-size:10px;color:#9db3e6}
.service .name{font-size:15px;font-weight:500;margin-top:2px}
.service svg{display:block;margin:0 auto 4px}

.card{position:absolute;top:1707px;width:322px;height:376px;border:1px solid #ddd;background:var(--white)}
.card .photo{height:230px}
.card h3{position:absolute;top:255px;width:100%;text-align:center;font-size:15px;font-weight:500}
.specs{position:absolute;top:292px;left:0;width:100%;display:flex;justify-content:space-around;font-size:11px;color:#555}
.specs span{display:flex;align-items:center;gap:6px}
.price-bar{position:absolute;bottom:0;left:0;width:100%;height:46px;display:flex;align-items:center;padding:0 6px}
.price-bar .price{width:132px;color:var(--white);font-size:12px;font-weight:500;padding-left:8px}
.price-bar .pid{flex:1;height:36px;background:var(--white);display:flex;align-items:center;justify-content:center;font-size:12px;font-weight:500}

.divider{position:absolute;left:99px;top:2140px;width:1002px;height:1px;background:#ccc}
.quote-box{position:absolute;left:147px;top:2277px;width:906px;height:245px;background:var(--blue);border-radius:24px;color:var(--white);text-align:center}
.quote-text{position:absolute;left:90px;width:726px;top:64px;font-size:11.5px;font-style:italic;line-height:25px}
.avatar{position:absolute;top:2565px;width:68px;height:68px;border-radius:50%;border:2px solid #eee}
.avatar.active{top:2557px;width:86px;height:86px}
.user-name{position:absolute;top:2651px;width:120px;text-align:center;font-size:12px;font-weight:500}

.site-footer{position:absolute;top:2718px;left:0;width:1200px;height:302px;background:var(--dark);color:var(--white)}
.footer-title{position:absolute;top:46px;font-size:18px;font-weight:500}
.footer-text{position:absolute;font-size:12px;line-height:24px}
.social{position:absolute;top:170px;left:99px;display:flex;gap:12px}
.social span{width:30px;height:30px;display:block}
.contact-line{position:absolute;display:flex;gap:14px;font-size:12px;line-height:22px}
</style>
</head>
<body>

<header class="site-header">
  <div class="brand">FERNCLIFF CAPITAL</div>
  <nav class="nav"><span>HOME</span><span>PROPERTY</span><span>OUR AGENTS</span><span>BLOG</span><span>ABOUT</span><span>CONTACT</span></nav>
</header>

<section class="hero" role="img" aria-label="Photo of an agent showing a smiling couple around a residential street"></section>
<div class="hero-box"></div>
<h1 class="hero-title center">FERNCLIFF CAPITAL</h1>
<p class="hero-sub center">Lorem ipsum dolor sit amet, consectetur adipiscing</p>
<div class="btn" style="left:533px;top:416px;width:134px;height:38px">READ MORE &gt;&gt;</div>

<h2 class="section-title center" style="top:588px">WELCOME TO FERNCLIFF CAPITAL</h2>
<p class="body-text" style="left:222px;top:646px;width:756px;text-align:center">Lorem ipsum dolor sit amet, consectetur adipiscing elit, sed do eiusmod tempor incididunt ut labore et dolore magna aliqua. Ut enim ad minim veniam, quis nostrud exercitation ullamco laboris nisi ut aliquip ex ea commodo consequat. Duis aute irure dolor in reprehenderit in voluptate velit esse cillum dolore eu fugiat nulla pariatur. Excepteur sint occaecat cupidatat non proident, sunt in culpa qui officia deserunt mollit anim id est laborum.Sed ut perspiciatis unde omnis iste natus error sit voluptatem accusantium doloremque laudantium,totam eaque ipsa quae ab illo inventore veritatis et quasi architecto beatae vitae</p>
<div class="btn" style="left:533px;top:804px;width:134px;height:36px">READ MORE &gt;&gt;</div>

<section class="contact-band" role="img" aria-label="Photo of a broker meeting with clients on a sofa"><div class="veil"></div></section>
<h2 class="section-title center" style="top:942px;color:var(--white)">REQUEST TO CONTACT US</h2>
<p class="abs center" style="top:988px;font-size:12px;font-weight:500;color:var(--white)">LOREM IPSUM DOLOR SIT AMET, CONSECTETUR ADIPISCING ELIT, SED DO EIUSMOD</p>
<div class="email-input" style="left:276px;top:1041px;width:469px;height:36px">Email ID...</div>
<div class="btn-square" style="left:765px;top:1041px;width:161px;height:36px;background:var(--blue)">SUBSCRIBE</div>

<section class="what-we-do"></section>
<h2 class="section-title" style="left:99px;top:1180px">WHAT WE DO</h2>
<p class="body-text" style="left:99px;top:1240px;width:485px">Lorem ipsum dolor sit amet, consectetur adipiscing elit, sed do eiusmod tempor incididunt ut labore et dolore magna aliqua. Ut enim ad minim veniam, quis nostrud exercitation ullamco laboris nisi ut aliquip ex ea commodo consequat. Duis aute irure dolor in reprehenderit in voluptate velit esse cillum dolore eu fugiat nulla pariatur.</p>
<p class="body-text" style="left:99px;top:1358px;width:485px">Excepteur sint occaecat cupidatat non proident, sunt in culpa qui officia deserunt mollit anim id est laborum.Ut enim ad minima veniam, quis nostrum exercitationem ullam corporis suscipit laboriosam, nisi ut aliquid.Quis autem vel eum iure reprehenderit qui in ea voluptate velit esse quam nihil molestiae consequatur,</p>
<div class="btn" style="left:99px;top:1484px;width:120px;height:32px">READ MORE &gt;&gt;</div>

<div class="services" role="img" aria-label="Photo of a modern house at dusk"></div>
<div class="service" style="left:664px;top:1222px">
  <svg width="56" height="56" viewBox="0 0 56 56"><circle cx="28" cy="28" r="27" fill="#f47a5f"/><circle cx="28" cy="22" r="9" fill="#2c3e50"/><path d="M12 48a16 14 0 0 1 32 0z" fill="#3a76c4"/></svg>
  <div class="cat">Estate Management</div><div class="name">MARKET EXPERT</div>
</div>
<div class="service" style="left:882px;top:1222px">
  <svg width="56" height="56" viewBox="0 0 56 56"><path d="M28 8 46 24H40V40H16V24H10z" fill="#fff"/><rect x="22" y="26" width="12" height="12" fill="#e04848"/><path d="M8 46h24l12-6" stroke="#fff" stroke-width="4" fill="none"/></svg>
  <div class="cat">Estate Management</div><div class="name">ESTATE INSURANCE</div>
</div>
<div class="service" style="left:664px;top:1368px">
  <svg width="56" height="56" viewBox="0 0 56 56"><circle cx="28" cy="28" r="27" fill="#3fb79a"/><rect x="17" y="12" width="22" height="30" fill="#fff"/><circle cx="30" cy="32" r="7" fill="none" stroke="#2c3e50" stroke-width="3"/></svg>
  <div class="cat">Estate Management</div><div class="name">MARKET ANALYSIS</div>
</div>
<div class="service" style="left:882px;top:1368px">
  <svg width="56" height="56" viewBox="0 0 56 56"><circle cx="28" cy="28" r="19" fill="#fff" stroke="#222" stroke-width="5"/><path d="M28 16 40 27H36V38H20V27H16z" fill="#e04848"/></svg>
  <div class="cat">Estate Management</div><div class="name">PROPERTY RESEARCH</div>
</div>

<h2 class="section-title center" style="top:1625px">FEATURED PROPERTIES</h2>

<article class="card" style="left:99px">
  <div class="photo" role="img" aria-label="Photo of a grey two-storey house with a porch" style="background:linear-gradient(180deg,#6f9bd6 0%,#8aa9c9 40%,#5e6669 70%,#4d6a35 100%)"></div>
  <h3>LOREM IPSUM DOLOR</h3>
  <div class="specs">
    <span><svg width="18" height="12"><rect x="1" y="5" width="16" height="5" fill="var(--blue)"/><rect x="1" y="1" width="4" height="4" fill="var(--blue)"/></svg>3 Beds</span>
    <span><svg width="14" height="16"><path d="M2 2h6v6h5v4H2z" fill="var(--blue)"/></svg>1 Bath</span>
    <span><svg width="16" height="16"><path d="M8 1 15 8H13V15H3V8H1z" fill="none" stroke="var(--blue)" stroke-width="2"/></svg>5 sqare feet</span>
  </div>
  <div class="price-bar" style="background:var(--blue)"><span class="price">£39420 / Day</span><span class="pid" style="color:var(--blue)">Property Id: 4287</span></div>
</article>

<article class="card" style="left:439px">
  <div class="photo" role="img" aria-label="Photo of a suburban house with garage and autumn tree" style="background:linear-gradient(180deg,#b9c8d6 0%,#8d8176 45%,#6e6660 70%,#5b7a3a 100%)"></div>
  <h3>LOREM IPSUM DOLOR</h3>
  <div class="specs">
    <span><svg width="18" height="12"><rect x="1" y="5" width="16" height="5" fill="var(--green)"/><rect x="1" y="1" width="4" height="4" fill="var(--green)"/></svg>3 Beds</span>
    <span><svg width="14" height="16"><path d="M2 2h6v6h5v4H2z" fill="var(--green)"/></svg>1 Bath</span>
    <span><svg width="16" height="16"><path d="M8 1 15 8H13V15H3V8H1z" fill="none" stroke="var(--green)" stroke-width="2"/></svg>5 sqare feet</span>
  </div>
  <div class="price-bar" style="background:var(--green)"><span class="price">£39420 / Day</span><span class="pid" style="color:var(--green)">Property Id: 4287</span></div>
</article>

<article class="card" style="left:779px">
  <div class="photo" role="img" aria-label="Photo of a yellow Mediterranean-style villa" style="background:linear-gradient(180deg,#5d93d8 0%,#9bb6d4 35%,#c9a866 60%,#5f8a3a 100%)"></div>
  <h3>LOREM IPSUM DOLOR</h3>
  <div class="specs">
    <span><svg width="18" height="12"><rect x="1" y="5" width="16" height="5" fill="var(--blue)"/><rect x="1" y="1" width="4" height="4" fill="var(--blue)"/></svg>3 Beds</span>
    <span><svg width="14" height="16"><path d="M2 2h6v6h5v4H2z" fill="var(--blue)"/></svg>1 Bath</span>
    <span><svg width="16" height="16"><path d="M8 1 15 8H13V15H3V8H1z" fill="none" stroke="var(--blue)" stroke-width="2"/></svg>5 sqare feet</span>
  </div>
  <div class="price-bar" style="background:var(--blue)"><span class="price">£39420 / Day</span><span class="pid" style="color:var(--blue)">Property Id: 4287</span></div>
</article>

<div class="divider"></div>
<h2 class="section-title center" style="top:2173px;font-size:26px">WHAT THEY SAY ABOUT US</h2>

<div class="quote-box">
  <div class="quote-text">Lorem ipsum dolor sit amet, consectetur adipiscing elit, sed do eiusmod tempor incididunt ut labore et dolore magna aliqua. Ut enim ad minim veniam, quis nostrud exercitation ullamco laboris nisi ut aliquip ex ea commodo consequat. Duis aute irure dolor in reprehenderit in voluptate velit esseExcepteur sint occaecat cupidatat non proident, sunt in culpa qui officia deserunt mollit anim id est laborum</div>
  <div class="abs" style="left:0;width:906px;top:156px;font-size:15px;font-weight:700">- HARUM QUIDEM</div>
  <div class="abs" style="left:0;width:906px;top:194px;font-size:11px">- CEO</div>
</div>
<svg class="abs" style="left:564px;top:2235px" width="72" height="72" viewBox="0 0 72 72"><circle cx="36" cy="36" r="34" fill="#fff"/><circle cx="36" cy="36" r="28" fill="var(--green)"/><path d="M24 42c0-8 3-12 8-14l1 3c-3 1-4 3-4 5h4v8h-9zM38 42c0-8 3-12 8-14l1 3c-3 1-4 3-4 5h4v8h-9z" fill="#fff"/></svg>
<svg class="abs" style="left:588px;top:2521px" width="24" height="26"><path d="M0 0h24L12 26z" fill="var(--blue)"/></svg>

<svg class="abs" style="left:144px;top:2589px" width="14" height="20"><path d="M12 0v20L0 10z" fill="var(--blue)"/></svg>
<svg class="abs" style="left:1040px;top:2589px" width="14" height="20"><path d="M2 0v20L14 10z" fill="var(--blue)"/></svg>
<div class="avatar" role="img" aria-label="Client portrait" style="left:208px;background:#c9b8a8"></div>
<div class="avatar" role="img" aria-label="Client portrait" style="left:391px;background:#d8c4b4"></div>
<div class="avatar active" role="img" aria-label="Client portrait" style="left:565px;background:#e2b84a"></div>
<div class="avatar" role="img" aria-label="Client portrait" style="left:757px;background:#8e8a86"></div>
<div class="avatar" role="img" aria-label="Client portrait" style="left:940px;background:#3c9ab0"></div>
<div class="user-name" style="left:182px">User Name</div>
<div class="user-name" style="left:365px">User Name</div>
<div class="user-name" style="left:548px">User Name</div>
<div class="user-name" style="left:731px">User Name</div>
<div class="user-name" style="left:914px">User Name</div>

<footer class="site-footer">
  <h4 class="footer-title" style="left:99px">ABOUT US</h4>
  <p class="footer-text" style="left:99px;top:82px;width:290px">Lorem ipsum dolor sit amet, consectetur adipiscing elit, sed do eiusmod tempor incididunt ut labore et dolore magna aliqua. Ut enim ad minim veniam</p>
  <div class="social"><span style="background:#3b5998"></span><span style="background:#1da1f2"></span><span style="background:#dd4b39"></span><span style="background:#8a3ab9"></span></div>

  <h4 class="footer-title" style="left:451px">CONTACT US</h4>
  <div class="contact-line" style="left:451px;top:76px"><svg width="10" height="22"><path d="M5 5a3 3 0 1 1 0 .1M5 15 1.5 8.5a4 4 0 1 1 7 0z" fill="#fff"/></svg><span>Lorem ipsum dolor sit amet, consectetur adipiscing<br>redo eiusmod tempor</span></div>
  <div class="contact-line" style="left:451px;top:124px"><svg width="10" height="22"><path d="M1 7c0 6 4 10 8 10l1-3-3-1-1 1c-2-1-3-3-3-4l1-1-1-3z" fill="#fff"/></svg><span>1-555-014-2277</span></div>
  <div class="contact-line" style="left:451px;top:154px"><svg width="10" height="22"><rect x="0" y="7" width="10" height="8" fill="#fff"/><path d="M0 7l5 4 5-4" stroke="#2b2b2b" fill="none"/></svg><span>info@ferncliffcapital.com</span></div>

  <h4 class="footer-title" style="left:827px">NEWSLETTER</h4>
  <div class="email-input" style="left:829px;top:100px;width:272px;height:37px">Email Id...</div>
  <div class="btn-square" style="left:829px;top:159px;width:272px;height:38px;background:var(--green)">SUBSCRIBE</div>

  <div class="abs" style="left:99px;top:243px;width:1002px;height:1px;background:#666"></div>
  <p class="abs center" style="top:265px;font-size:12px">Copyright 2017 - Ferncliff Capital.Allrights Reserved.</p>
</footer>

</body>
</html>
```